Brellwick Partners, LLC Stationary

Brellwick Partners, LLC is a new financial planning and consulting company. We are looking for designs on business cards, letterhead, envelopes, and anything else that would be useful. Our preference for business card design is two sided. We are looking for a professional and clean look with incorporating the logo and patriotic feel. Thank you to all who participate and good luck!

```html
<!DOCTYPE html>
<html lang="en">
<head>
<meta charset="utf-8">
<title>Brellwick Partners, LLC Stationery</title>
<link href="https://fonts.googleapis.com/css2?family=Arimo:wght@400;700&family=Montserrat:wght@600&display=swap" rel="stylesheet">
<style>
  :root {
    --backdrop: #a9a7a8;
    --paper: #f4f3f1;
    --white: #ffffff;
    --navy: #123e6b;
    --red: #c6232b;
    --ink: #555555;
    --faint: rgba(18, 62, 107, 0.05);
  }
  * { margin: 0; padding: 0; box-sizing: border-box; }
  html, body { width: 1200px; height: 770px; overflow: hidden; }
  body {
    background: var(--backdrop);
    position: relative;
    font-family: "Arimo", Arial, sans-serif;
    color: var(--ink);
  }
  .piece {
    position: absolute;
    background: var(--paper);
    box-shadow: 2px 3px 8px rgba(0,0,0,0.25);
    overflow: hidden;
  }
  .brand-band {
    position: absolute; left: 0; right: 0; bottom: 0;
    background: var(--red);
  }
  .brand-band .navy-part {
    position: absolute; left: 0; top: 0; bottom: 0;
    background: var(--navy);
    clip-path: polygon(0 0, 100% 0, calc(100% - 4px) 100%, 0 100%);
  }
  .brand-band .gap {
    position: absolute; top: 0; bottom: 0; width: 3px;
    background: var(--paper);
    transform: skewX(-18deg);
  }
  .wordmark {
    position: absolute;
    display: flex; align-items: center; gap: 6px;
    font-family: "Montserrat", Arial, sans-serif;
    font-weight: 600;
    color: var(--navy);
    letter-spacing: 0.04em;
    line-height: 1.05;
  }
  .wordmark .dot { border-radius: 50%; background: var(--red); flex: none; }
  .wordmark.on-dark { color: var(--white); }
  .wordmark.on-dark .dot { background: var(--white); }
  .tagline {
    position: absolute;
    font-size: 4px; letter-spacing: 0.12em; text-transform: uppercase;
    color: var(--navy);
  }
  .faint-disc {
    position: absolute; border-radius: 50%;
    background: var(--faint);
  }

  /* Business card front */
  .card-front { left: 86px; top: 46px; width: 218px; height: 124px; background: var(--white); }
  .card-front .brand-band { height: 7px; }
  .card-front .divider { position: absolute; left: 117px; top: 26px; width: 1px; height: 68px; background: #c9c9c9; }
  .card-front .person { position: absolute; left: 125px; top: 25px; }
  .person .name { font-size: 7px; font-weight: 700; color: var(--navy); }
  .person .role { font-size: 5px; color: var(--red); margin-top: 1px; }
  .person .address { font-size: 5px; margin-top: 6px; line-height: 1.6; }
  .contact-list { list-style: none; }
  .contact-list li { display: flex; align-items: center; gap: 3px; }
  .contact-list svg { fill: var(--navy); flex: none; }
  .person .contact-list { font-size: 5px; line-height: 1.7; margin-top: 1px; }

  /* Business card back */
  .card-back { left: 338px; top: 46px; width: 218px; height: 124px; background: var(--navy); }
  .card-back .web { position: absolute; left: 0; right: 0; top: 103px; text-align: center; font-size: 5px; letter-spacing: 0.35em; color: var(--white); }

  /* Envelope front */
  .envelope-front { left: 62px; top: 202px; width: 560px; height: 255px; }
  .envelope-front .brand-band { height: 12px; }
  .envelope-front .address { position: absolute; left: 24px; top: 68px; font-size: 9px; line-height: 1.3; color: var(--ink); }

  /* Envelope back */
  .envelope-back { left: 57px; top: 480px; width: 559px; height: 254px; }
  .envelope-back .flap { position: absolute; left: 0; top: 0; }
  .envelope-back .web { position: absolute; left: 0; right: 0; top: 69px; text-align: center; font-size: 7px; letter-spacing: 0.18em; color: var(--white); }

  /* Letterhead */
  .letterhead { left: 643px; top: 33px; width: 497px; height: 701px; }
  .letterhead .brand-band { height: 11px; }
  .letterhead .footer-contact { position: absolute; left: 31px; top: 641px; font-size: 8.5px; line-height: 1.45; color: var(--ink); }
  .letterhead .footer-address { position: absolute; right: 32px; top: 644px; text-align: right; font-size: 8.5px; line-height: 1.4; }
  .letterhead .footer-address .web { color: var(--navy); letter-spacing: 0.12em; }
</style>
</head>
<body>

  <!-- Business card: front -->
  <section class="piece card-front">
    <div class="wordmark" style="left:14px; top:46px; font-size:8px; gap:4px;">
      <span class="dot" style="width:7px;height:7px;"></span>
      <span>BRELLWICK<br>PARTNERS, LLC</span>
    </div>
    <div class="divider"></div>
    <div class="person">
      <p class="name">MARA COLVIN</p>
      <p class="role">PRESIDENT</p>
      <p class="address">2176 Aldergate Lane<br>Hollis Bay, NY 11420</p>
      <ul class="contact-list">
        <li><svg width="5" height="5" viewBox="0 0 10 10"><path d="M2 1h2l1 2-1.5 1a6 6 0 0 0 2.5 2.5L7 5l2 1v2c0 .6-.4 1-1 1A8 8 0 0 1 1 2c0-.6.4-1 1-1z"/></svg>512 7739 1048</li>
        <li><svg width="5" height="5" viewBox="0 0 10 10"><path d="M3 1h4v2H3zM1 4h8v4H7v1H3V8H1z"/></svg>640 2281 5937</li>
        <li><svg width="5" height="5" viewBox="0 0 10 10"><path d="M1 2h8v6H1zM1 2l4 3 4-3" /></svg>mara@brellwick.com</li>
        <li><svg width="5" height="5" viewBox="0 0 10 10"><circle cx="5" cy="5" r="4"/></svg>www.brellwick.com</li>
      </ul>
    </div>
    <div class="brand-band"><div class="navy-part" style="width:142px;"></div></div>
  </section>

  <!-- Business card: back -->
  <section class="piece card-back">
    <div class="wordmark on-dark" style="left:46px; top:54px; font-size:10px;">
      <span class="dot" style="width:9px;height:9px;"></span>
      <span>BRELLWICK PARTNERS, LLC</span>
    </div>
    <p class="web">www.brellwick.com</p>
  </section>

  <!-- Envelope: front -->
  <section class="piece envelope-front">
    <div class="faint-disc" role="img" aria-label="Faint brand decoration" style="left:320px; top:10px; width:230px; height:230px;"></div>
    <div class="wordmark" style="left:26px; top:30px; font-size:13px;">
      <span class="dot" style="width:12px;height:12px;"></span>
      <span>BRELLWICK PARTNERS, LLC</span>
    </div>
    <p class="tagline" style="left:46px; top:50px;">Financial Planning and Consulting</p>
    <p class="address">2176 Aldergate Lane<br>Hollis Bay, NY 11420</p>
    <div class="brand-band"><div class="navy-part" style="width:391px;"></div></div>
  </section>

  <!-- Envelope: back -->
  <section class="piece envelope-back">
    <svg class="flap" width="559" height="96" viewBox="0 0 559 96" aria-hidden="true">
      <path d="M0 0H559L548 62C545 82 534 93 510 93H49C25 93 14 82 11 62Z" fill="var(--navy)"/>
    </svg>
    <div class="wordmark on-dark" style="left:0; right:0; top:44px; justify-content:center; font-size:10px;">
      <span class="dot" style="width:9px;height:9px;"></span>
      <span>BRELLWICK PARTNERS, LLC</span>
    </div>
    <p class="web">www.brellwick.com</p>
  </section>

  <!-- Letterhead -->
  <section class="piece letterhead">
    <div class="faint-disc" role="img" aria-label="Faint brand decoration" style="left:80px; top:220px; width:400px; height:400px;"></div>
    <div class="wordmark" style="left:31px; top:54px; font-size:14px;">
      <span class="dot" style="width:13px;height:13px;"></span>
      <span>BRELLWICK PARTNERS, LLC</span>
    </div>
    <p class="tagline" style="left:52px; top:76px;">Financial Planning and Consulting</p>

    <ul class="contact-list footer-contact">
      <li><svg width="8" height="8" viewBox="0 0 10 10"><path d="M2 1h2l1 2-1.5 1a6 6 0 0 0 2.5 2.5L7 5l2 1v2c0 .6-.4 1-1 1A8 8 0 0 1 1 2c0-.6.4-1 1-1z"/></svg>512 7739 1048</li>
      <li><svg width="8" height="8" viewBox="0 0 10 10"><path d="M3 1h4v2H3zM1 4h8v4H7v1H3V8H1z"/></svg>640 2281 5937</li>
      <li><svg width="8" height="8" viewBox="0 0 10 10"><path d="M1 2h8v6H1z"/></svg>mara@brellwick.com</li>
    </ul>
    <p class="footer-address">2176 Aldergate Lane<br>Hollis Bay, NY 11420<br><span class="web">www.brellwick.com</span></p>
    <div class="brand-band"><div class="navy-part" style="width:328px;"></div></div>
  </section>

</body>
</html>
```